Fenwick Grading LTD - website for irrigation & Landscape Lighting & Buried service wire

Looking for a website to help promote my business with Irrigation (installation, service, etc) and buried service wire/drainage solutions.

Commercial/Residential

Landscape lighting.

I’ll get photos in the trucks and trailers to upload as well maybe the machine as well.

Target Market(s)

Homeowners who want green grass and beautiful gardens. Beautiful landscape lighting

Industry/Entity Type

Irrigation systems and landscape lighting and buried service wire to homes and offering Drainage soltions.

Coding

Coded - Design and coding required

Number of Pages Required

4 page

Colors
F0912C
F2A743
F7CA91
FBE8D2
FDF5EE

Requirements
Must have
• was hoping to link up my email on fenwickgrading@mailbox-example.net with the website if possible.
Nice to have
• Page for Irrigation, page for landscape lighting, page buried service wire & drainage soltions.

```html
<!DOCTYPE html>
<html lang="en">
<head>
<meta charset="utf-8">
<title>Landscape Lighting – Fenwick Grading LTD</title>
<link rel="stylesheet" href="https://fonts.googleapis.com/css2?family=Montserrat:wght@400;500;600;700&family=Roboto+Condensed:wght@600;700&display=swap">
<style>
:root{
  --orange:#F0912C;
  --amber:#F2A743;
  --peach:#F7CA91;
  --cream:#FBE8D2;
  --shell:#FDF5EE;
  --ink:#111111;
  --text:#444444;
  --muted:#666666;
  --white:#ffffff;
}
*{box-sizing:border-box;margin:0;padding:0}
html,body{width:1200px;height:3883px;overflow:hidden;background:var(--white)}
body{position:relative;font-family:'Montserrat',sans-serif;color:var(--text)}
.abs{position:absolute}
.heading{font-family:'Roboto Condensed',sans-serif;font-weight:700;color:var(--ink);text-align:center;font-size:40px;line-height:1.15}
.heading .accent{color:var(--orange)}
.center{left:0;width:1200px;text-align:center}

/* hero */
.hero{left:0;top:0;width:1200px;height:440px}
.hero svg{display:block}
.brand{font-family:'Montserrat',sans-serif;font-weight:700;color:var(--orange);font-size:22px;line-height:1;display:flex;align-items:center;gap:10px}
.brand .dot{width:14px;height:14px;background:var(--orange);border-radius:50%}
.nav{top:32px;left:408px;display:flex;gap:44px;font-size:14px;color:var(--white)}
.nav .active{color:var(--orange);text-decoration:underline;text-underline-offset:5px}
.btn{display:inline-block;background:var(--orange);color:var(--white);font-weight:600;font-size:12px;letter-spacing:.5px;border-radius:20px;text-align:center}
.hero-title{left:141px;top:186px;font-family:'Roboto Condensed',sans-serif;font-weight:700;font-size:40px;color:var(--white)}
.crumb{left:141px;top:232px;font-size:13px;color:var(--white)}
.crumb b{font-weight:600}

.lead{font-size:13px;color:var(--ink);font-weight:500;line-height:22px}
.body-copy{font-size:13px;line-height:22px;color:var(--muted)}

/* features */
.feature{width:220px;top:927px;height:324px;text-align:center;padding:32px 12px 0}
.feature.raised{border:1px solid var(--cream);border-radius:18px;box-shadow:0 6px 18px rgba(240,145,44,.08)}
.feature .icon{width:86px;height:86px;margin:0 auto 20px;border-radius:50%;border:1.5px solid var(--orange);display:flex;align-items:center;justify-content:center}
.feature.raised .icon{background:var(--orange);border-color:var(--orange)}
.feature h3{font-size:14px;font-weight:500;color:var(--ink);margin-bottom:10px}
.feature p{font-size:10.5px;line-height:17.5px;color:var(--muted)}

/* steps */
.step-text{width:420px}
.step-text h4{font-size:14px;font-weight:500;color:var(--ink);border-left:2px solid var(--orange);padding:10px 0 10px 12px;margin-bottom:26px}
.step-text p{font-size:13.2px;line-height:22.6px;color:var(--muted)}

/* band */
.band{left:0;top:2977px;width:1200px;height:394px;background:var(--shell)}

/* footer */
.footer-nav{top:3697px;left:0;width:1200px;display:flex;justify-content:center;gap:56px;font-size:13px;color:var(--white)}
.footer-nav .active{color:var(--orange)}
.contact{display:flex;gap:12px;align-items:center;color:var(--white);font-size:13px;line-height:20px}
.contact .ring{width:36px;height:36px;border-radius:50%;border:1.5px solid var(--orange);display:flex;align-items:center;justify-content:center;flex:none}
.social{display:flex;gap:8px}
.social span{width:32px;height:32px;border-radius:50%;border:1.5px solid var(--orange);display:block}
</style>
</head>
<body>

<!-- hero -->
<div class="abs hero">
  <svg width="1200" height="440" viewBox="0 0 1200 440" role="img" aria-label="Evening garden with curved stone wall, lawn and a glowing lighting bollard">
    <defs>
      <linearGradient id="heroFill" x1="0" y1="0" x2="1" y2="1">
        <stop offset="0" stop-color="#2f3a22"/>
        <stop offset=".45" stop-color="#4a5a2a"/>
        <stop offset=".75" stop-color="#5c6a30"/>
        <stop offset="1" stop-color="#2a2e1c"/>
      </linearGradient>
    </defs>
    <path d="M0 0H1200V355L600 438 0 368Z" fill="var(--orange)"/>
    <path d="M0 0H1200V350L600 425 0 362Z" fill="url(#heroFill)"/>
    <path d="M0 0H1200V350L600 425 0 362Z" fill="#000" opacity=".28"/>
  </svg>
</div>
<div class="abs brand" style="left:141px;top:40px"><span class="dot"></span>Fenwick Grading LTD</div>
<nav class="abs nav">
  <span>Home</span><span>Irrigation</span><span class="active">Landscape Lighting</span><span>Trenching&nbsp; Services</span>
</nav>
<span class="abs btn" style="left:940px;top:26px;width:118px;height:33px;line-height:33px">CONTACT US</span>
<h1 class="abs hero-title">Landscape Lighting</h1>
<div class="abs crumb">Home » <b>Landscape Lighting</b></div>

<!-- intro -->
<h2 class="abs heading center" style="top:526px">Landscape <span class="accent">Lighting</span></h2>
<p class="abs lead center" style="top:585px">Illuminating Your Outdoor Space with Stunning Landscape Lighting</p>
<p class="abs body-copy" style="left:140px;top:622px;width:928px;text-align:center">FenwickGrading Irrigation Systems, specializes in creating breathtaking landscape lighting designs that will transform your outdoor space into a captivating oasis. With our expertise and attention to detail, we can enhance the beauty, functionality, and security of your property while creating a welcoming ambiance for outdoor gatherings.</p>

<!-- why -->
<h2 class="abs heading center" style="top:773px">Why Choose <span class="accent">Landscape Lighting</span></h2>
<p class="abs lead center" style="top:832px;font-size:13px">For a convenient way to send us your inquiries, you<br>can use our contact form. Simply fill in the required fields, and we'll respond promptly.</p>

<div class="abs feature" style="left:141px">
  <div class="icon"><svg width="40" height="40" viewBox="0 0 40 40" fill="none" stroke="var(--orange)" stroke-width="1.8"><circle cx="18" cy="22" r="11"/><path d="M30 6l1.5 3 3 1.5-3 1.5L30 15l-1.5-3-3-1.5 3-1.5z"/></svg></div>
  <h3>Enhanced Aesthetics</h3>
  <p>Properly designed and placed lighting fixtures can accentuate the architectural features of your home, highlight beautiful trees and plants, and create focal points that draw attention to specific areas of your landscape.<br>clear</p>
</div>
<div class="abs feature raised" style="left:372px">
  <div class="icon"><svg width="40" height="40" viewBox="0 0 40 40" fill="none" stroke="var(--white)" stroke-width="1.8"><circle cx="20" cy="18" r="12"/><circle cx="20" cy="18" r="5"/><path d="M14 30v6M26 30v6"/></svg></div>
  <h3>Increased Functionality</h3>
  <p>Landscape lighting allows you to enjoy your outdoor living spaces long after the sun sets. Whether you want to host evening gatherings or relax with a book on your patio, our strategically placed lighting fixtures will provide the perfect illumination.</p>
</div>
<div class="abs feature" style="left:605px">
  <div class="icon"><svg width="40" height="40" viewBox="0 0 40 40" fill="none" stroke="var(--orange)" stroke-width="1.8"><circle cx="20" cy="20" r="9"/><path d="M20 15v10M15 20h10M4 28c6 6 26 6 32 0"/></svg></div>
  <h3>Safety and Security</h3>
  <p>A well-lit exterior can deter potential intruders, provide visibility and safety for your guests, and help prevent accidents by illuminating potential trip hazards and obstacles.</p>
</div>
<div class="abs feature" style="left:837px">
  <div class="icon"><svg width="40" height="40" viewBox="0 0 40 40" fill="none" stroke="var(--orange)" stroke-width="1.8"><path d="M22 6l-8 14h8l-4 12 10-16h-8z"/><path d="M4 24c2 8 8 12 12 12M36 24c-2 8-8 12-12 12"/></svg></div>
  <h3>Energy Efficiency</h3>
  <p>We prioritize energy efficiency by utilizing state-of-the-art LED lighting technology. LED bulbs last longer, consume less electricity, and emit less heat compared to traditional lighting options, resulting in reduced energy costs and less environmental impact.</p>
</div>

<!-- approach -->
<h2 class="abs heading center" style="top:1331px">Our Approach To <span class="accent">Landscape Lighting</span></h2>
<p class="abs lead center" style="top:1390px;font-size:13px">At FenwickGrading Irrigation Systems, we believe that each outdoor space is unique and deserves a customized<br>lighting design. Our process involves</p>

<svg class="abs" style="left:176px;top:1503px" width="326" height="292" viewBox="0 0 326 292" role="img" aria-label="Two women in a garden shop reviewing a tablet">
  <defs><linearGradient id="g1" x1="0" y1="0" x2="1" y2="1"><stop offset="0" stop-color="#7d8a5c"/><stop offset=".5" stop-color="#c7ab8c"/><stop offset="1" stop-color="#3a3a34"/></linearGradient></defs>
  <polygon points="0,0 316,0 158,280" fill="url(#g1)"/>
  <polyline points="0,0 164,290 326,0" fill="none" stroke="var(--orange)" stroke-width="2"/>
</svg>
<div class="abs step-text" style="left:613px;top:1566px"><h4>Consultation</h4><p>We begin by understanding your vision, preferences, and specific requirements. Our experienced lighting designers will discuss your ideas and provide expert guidance to ensure that your lighting design aligns perfectly with your outdoor space and personal style.</p></div>

<svg class="abs" style="left:696px;top:1883px" width="326" height="292" viewBox="0 0 326 292" role="img" aria-label="Aerial view of a landscaped yard with paths and trees">
  <defs><linearGradient id="g2" x1="0" y1="0" x2="0" y2="1"><stop offset="0" stop-color="#4e6a34"/><stop offset=".5" stop-color="#8f8a62"/><stop offset="1" stop-color="#3f5e2a"/></linearGradient></defs>
  <polygon points="0,0 316,0 158,280" fill="url(#g2)"/>
  <polyline points="0,0 164,290 326,0" fill="none" stroke="var(--orange)" stroke-width="2"/>
</svg>
<div class="abs step-text" style="left:176px;top:1946px"><h4>Design and Planning</h4><p>Our team will create a detailed lighting plan, considering factors such as the layout of your property, focal points, key features, and desired lighting effects. We utilize cutting-edge design tools to showcase a virtual representation of your landscape lighting vision.</p></div>

<svg class="abs" style="left:176px;top:2263px" width="326" height="292" viewBox="0 0 326 292" role="img" aria-label="Gardener in an apron tending plants">
  <defs><linearGradient id="g3" x1="0" y1="0" x2="1" y2="1"><stop offset="0" stop-color="#6f8a4a"/><stop offset=".5" stop-color="#b9b6a6"/><stop offset="1" stop-color="#2f5b4a"/></linearGradient></defs>
  <polygon points="0,0 316,0 158,280" fill="url(#g3)"/>
  <polyline points="0,0 164,290 326,0" fill="none" stroke="var(--orange)" stroke-width="2"/>
</svg>
<div class="abs step-text" style="left:613px;top:2326px"><h4>Installation</h4><p>Our skilled technicians will expertly install your landscape lighting system, following industry standards and taking care of every detail. We ensure precise fixture placement, conceal wiring, and optimize the power source for a seamless and professional installation</p></div>

<svg class="abs" style="left:696px;top:2600px" width="326" height="292" viewBox="0 0 326 292" role="img" aria-label="Two gardeners working outdoors among greenery">
  <defs><linearGradient id="g4" x1="0" y1="0" x2="1" y2="1"><stop offset="0" stop-color="#5f7d3c"/><stop offset=".55" stop-color="#c9a88a"/><stop offset="1" stop-color="#8a3a34"/></linearGradient></defs>
  <polygon points="0,0 316,0 158,280" fill="url(#g4)"/>
  <polyline points="0,0 164,290 326,0" fill="none" stroke="var(--orange)" stroke-width="2"/>
</svg>
<div class="abs step-text" style="left:176px;top:2679px"><h4>Maintenance and Upgrades</h4><p>We offer regular maintenance packages to keep your landscape lighting in optimal condition. Additionally, if you ever want to expand your existing system or upgrade to the latest technology, our team will be there to assist you.</p></div>

<!-- band -->
<div class="abs band"></div>
<h2 class="abs heading center" style="top:3028px;line-height:56px">Experience The Difference With<br><span class="accent">FenwickGrading Irrigation Systems</span></h2>
<p class="abs center" style="top:3141px;font-size:13px;line-height:22.6px;font-weight:600;color:var(--ink)">With years of experience and a passion for creating captivating outdoor lighting designs, [Your Company Name] is<br>committed to exceeding your expectations. Our attention to detail, use of high-quality materials, and dedication to<br>customer satisfaction are what set us apart.</p>
<p class="abs center" style="top:3215px;font-size:13px;line-height:22.6px;color:var(--text)">Take the first step toward transforming your outdoor space with mesmerizing landscape lighting. Contact [Your<br>Company Name] today for a consultation, and let our expert team bring your vision to life.</p>
<span class="abs btn" style="left:548px;top:3278px;width:104px;height:34px;line-height:34px">CONTACT</span>

<!-- footer -->
<svg class="abs" style="left:0;top:3455px" width="1200" height="428" viewBox="0 0 1200 428">
  <path d="M0 82L600 0 1200 82V428H0Z" fill="var(--orange)"/>
  <path d="M0 90L600 9 1200 90V428H0Z" fill="#000"/>
</svg>
<div class="abs brand" style="left:0;width:1200px;justify-content:center;top:3600px;font-size:28px"><span class="dot"></span>Fenwick Grading LTD</div>
<nav class="abs footer-nav"><span>Home</span><span class="active">Irrigation</span><span>Landscape Lighting</span><span>Trenching&nbsp; Services</span><span style="font-weight:600">Contact Us</span></nav>

<div class="abs contact" style="left:207px;top:3755px">
  <span class="ring"><svg width="14" height="18" viewBox="0 0 14 18"><path d="M7 0C3 0 0 3 0 7c0 5 7 11 7 11s7-6 7-11c0-4-3-7-7-7z" fill="var(--white)"/><circle cx="7" cy="7" r="2.5" fill="#000"/></svg></span>
  <span>123, Building Name, Street<br>City, State XY 123456</span>
</div>
<div class="abs contact" style="left:527px;top:3755px">
  <span class="ring"><svg width="16" height="16" viewBox="0 0 24 24"><path d="M6.6 10.8a15 15 0 006.6 6.6l2.2-2.2c.3-.3.7-.4 1-.2 1.1.4 2.3.6 3.6.6.6 0 1 .4 1 1V20c0 .6-.4 1-1 1A17 17 0 013 4c0-.6.4-1 1-1h3.5c.6 0 1 .4 1 1 0 1.3.2 2.5.6 3.6.1.3 0 .7-.2 1z" fill="var(--white)"/></svg></span>
  <span>Phone<br>123-456-7890</span>
</div>
<div class="abs contact" style="left:764px;top:3755px">
  <span class="ring"><svg width="16" height="12" viewBox="0 0 16 12"><rect width="16" height="12" rx="1.5" fill="var(--white)"/><path d="M1 1l7 5 7-5" fill="none" stroke="#000" stroke-width="1.4"/></svg></span>
  <span>E-Mail<br>info@fenwickgrading.example</span>
</div>

<div class="abs" style="left:141px;top:3840px;font-size:13px;color:var(--white)">© 2024 Fenwick Grading LTD . All Rights Reserved.</div>
<div class="abs social" style="left:904px;top:3833px"><span></span><span></span><span></span><span></span></div>

</body>
</html>
```